Catalogue Design Project

We need a catalog design for a new private university called Redwell Institute Bayshore (see website www.rwi-bs.org). The catalog should be about 30 pages maximum and will include items such as General Information, Academic schedule, department descriptions, program descriptions, course descriptions, school policies, student services, admissions, San diego Lifestyle, etc.
I will provide the text but I need a professional design with regard to page layouts. I have provided some examples.
Ok, i posted the catalog content, just missing course descriptions.
Target Market(s)
Young Professionals, Foreign Students
Industry/Entity Type
University
Look and feel
Each slider illustrates characteristics of the customer's brand and the style your logo design should communicate.

```html
<!DOCTYPE html>
<html lang="en">
<head>
<meta charset="utf-8">
<title>Academic Programs – TESOL Certificate</title>
<link rel="stylesheet" href="https://fonts.googleapis.com/css2?family=Carlito:wght@400;700&display=swap">
<style>
  :root {
    --ink: #1a1a1a;
    --blue: #2f5f93;
    --blue-dark: #1c3f66;
    --blue-light: #6f93bb;
    --rule: #9fb3c8;
    --grey: #8a8a8a;
    --paper: #ffffff;
    --photo-warm: #d9c7a6;
    --photo-pale: #efe6d4;
  }
  * { margin: 0; padding: 0; box-sizing: border-box; }
  html, body { width: 927px; height: 1200px; overflow: hidden; background: var(--paper); }
  .page {
    position: relative; width: 927px; height: 1200px;
    font-family: "Carlito", "Calibri", sans-serif; color: var(--ink);
  }
  .brand-dots {
    position: absolute; left: 58px; top: 58px; width: 154px; height: 34px;
    background: linear-gradient(90deg, #8f9aa6, var(--blue));
    border-radius: 17px; opacity: .55;
  }
  .header-photo {
    position: absolute; right: 0; top: 0; width: 360px; height: 150px;
    background: linear-gradient(90deg, rgba(255,255,255,1) 0%, var(--photo-pale) 35%, var(--photo-warm) 100%);
  }
  .section-title {
    position: absolute; left: 0; width: 927px; top: 92px;
    text-align: center; font-size: 31px; font-weight: 400; letter-spacing: .3px;
    color: var(--ink);
  }
  .header-rule { position: absolute; left: 0; top: 149px; width: 927px; height: 2px; background: var(--rule); }
  .header-bar { position: absolute; left: 305px; top: 133px; width: 318px; height: 17px; background: var(--blue); }
  .tab-band {
    position: absolute; left: 0; top: 192px; width: 60px; height: 25px;
    background: linear-gradient(90deg, #d8e2ee, var(--blue-light));
  }
  .tab {
    position: absolute; left: 42px; top: 178px; width: 382px; height: 40px;
    background: linear-gradient(180deg, var(--blue-light) 0%, var(--blue) 45%, var(--blue-dark) 100%);
    border-radius: 4px 14px 14px 4px;
    color: #fff; font-size: 29px; line-height: 40px; padding-left: 22px; letter-spacing: .3px;
  }
  .program {
    position: absolute; left: 79px; top: 244px; width: 804px;
    font-size: 20px; line-height: 35px;
  }
  .program h2 { text-align: center; font-size: 24px; font-weight: 700; line-height: 38px; margin-bottom: 4px; }
  .program p { text-align: justify; }
  .program .gap { height: 35px; }
  .label { font-weight: 700; }
  .underlined { text-decoration: underline; }
  .footer-rule { position: absolute; left: 0; top: 1158px; width: 927px; height: 1px; background: var(--rule); }
  .footer-mark {
    position: absolute; right: 41px; top: 1169px;
    font-size: 13px; color: var(--grey); letter-spacing: .3px;
  }
</style>
</head>
<body>
<div class="page">
  <div class="brand-dots" role="img" aria-label="Dot pattern brand decoration"></div>
  <div class="header-photo" role="img" aria-label="Photo of an open antique book"></div>
  <h1 class="section-title">ACADEMIC PROGRAMS</h1>
  <div class="header-bar"></div>
  <div class="header-rule"></div>

  <div class="tab-band"></div>
  <div class="tab">CERTIFICATE PROGRAMS</div>

  <section class="program">
    <h2>TESOL Certificate</h2>
    <p>The Certificate in Teaching-English-to-Speakers-of-Other-Languages (TESOL) offers coursework which allows participants to acquire the specialized training and skills needed for a successful career teaching English as a second language, either in the U.S. or in another country. Emphasis is placed on essential ESL skills ranging from teaching pronunciation, listening, speaking, writing, and classroom management to specialized teaching skills such as teaching Business English and children, as well as tutoring private students.</p>
    <p>The fundamentals of English grammar and how to teach it through stimulating and engaging lessons are also emphasized. In addition to in-classroom training, students will also participate in teaching actual foreign students currently studying English. Students of the TESOL certificate program will receive weekly progress reports in addition to ample experience to ensure readiness at time of graduation.</p>
    <p>Completion and attainment of TESOL Credential improves successful job offers, and thus finally, the course will offer job information for teachers looking to obtain positions overseas. Our internationally experienced teachers focus on ensuring your passport to success.</p>
    <p><span class="label">Hours:</span> 15 hours per week</p>
    <p><span class="label">Length:</span> 5 weeks per course</p>
    <div class="gap"></div>
    <p class="underlined">Course:</p>
    <p>ENG 600 TESOL</p>
    <p class="underlined">Learning Outcome:</p>
    <p>Gain the needed instruction and experience to become a teacher of English either in the United States or abroad.</p>
  </section>

  <div class="footer-rule"></div>
  <div class="footer-mark">7::: REDWELL INSTITUTE</div>
</div>
</body>
</html>
```